International Clinical Software Company needs a new business card design

We are looking for a new business card design for our company that has recently expanded into the UK market, making us a multinational company.
After having rebranded our website and produced a new style guide, we are looking for a business card that is creative and attention grabbing, while being consistent with the style and colour scheme used on the new website, www.plumvora.example
We produce care management technology for the aged care market, but the main aspect we aim to communicate is the human element of our software, and the way it assists in providing better care for aged people, and stronger relationships between aged people and the staff that care for them.
Our current business card is a dark green with gold text, which makes the text quite difficult to read, not very aesthetically appealing and the colour scheme looks quite dated.
We would like something fresh and modern, that can still be colourful but doesn't use large blocks of dark colour, and uses the colours within our logo.
Something tying in with the leaves that are used in our logo could work quite nicely, along with the Autumn/Fall colours of soft greens, yellows and reds (also in our existing logo). However also happy to look at fresh, completely out of the box ideas we may not have yet considered.
Target Market(s)
The people that receive this business card work in the aged card or health industry and are either corporate/management level staff or clinical (Registered Nurses, care workers etc.)
Industry/Entity Type
Health Product
Contact Information for Business Card
Company Name - BrindlewayCare
Company locations: United Kingdom, Australia, New Zealand
Staff Details:
Staff name: Derek Mallow
Staff job title: Executive Chairman
Staff email: d.mallow@plumvora.example
Office phone number: 01742 918576
Font styles to use
Other font styles liked:
- Calibri
Requirements
Must have
- Must include the BrindlewayCare brand name in it's current font
- Must include logo (3 leaves in gold circle)
- Must include Business Card Details
Nice to have
- Elements of gold
- White space
- Something autumn themed but not too cliched
Should not have
- No blue - used by a major competitor and we would like to differentiate from them
- Large blocks of dark green colour (the green that appears in our leaves on the logo on our current business card is the background colour and it is far too dark)

```html
<!DOCTYPE html>
<html lang="en">
<head>
<meta charset="utf-8">
<title>BrindlewayCare Business Card</title>
<link rel="stylesheet" href="https://fonts.googleapis.com/css2?family=Lato:wght@300;400;700&display=swap">
<style>
  :root {
    --bg: #ece9e4;
    --card: #ffffff;
    --crimson: #b3124a;
    --gold: #b8a27b;
    --text-grey: #6f6f6f;
    --icon-grey: #9a8f7e;
  }
  html, body {
    margin: 0;
    padding: 0;
    width: 1200px;
    height: 950px;
    overflow: hidden;
    background: var(--bg);
  }
  .canvas {
    position: relative;
    width: 1200px;
    height: 950px;
    display: flex;
    align-items: center;
    justify-content: center;
  }
  .card {
    position: relative;
    width: 900px;
    height: 540px;
    background: var(--card);
    border-radius: 34px;
    box-shadow: 0 10px 30px rgba(0, 0, 0, 0.12);
    overflow: hidden;
    font-family: "Lato", sans-serif;
  }
  .accent-band {
    position: absolute;
    top: 0;
    left: 664px;
    width: 128px;
    height: 170px;
    background: var(--crimson);
  }
  .brand-dot {
    position: absolute;
    left: 664px;
    top: 110px;
    width: 128px;
    height: 128px;
    border-radius: 50%;
    background: var(--gold);
    border: 5px solid var(--card);
    box-sizing: border-box;
  }
  .brand-name {
    position: absolute;
    left: 704px;
    top: 256px;
    width: 48px;
    margin: 0;
    writing-mode: vertical-rl;
    transform: rotate(180deg);
    font-weight: 300;
    font-size: 38px;
    line-height: 48px;
    letter-spacing: 1px;
    color: var(--gold);
    white-space: nowrap;
  }
  .person {
    position: absolute;
    left: 62px;
    top: 70px;
  }
  .person-name {
    margin: 0;
    font-weight: 700;
    font-size: 34px;
    color: var(--gold);
  }
  .person-title {
    margin: 4px 0 0;
    font-weight: 400;
    font-size: 26px;
    color: var(--crimson);
  }
  .contact {
    position: absolute;
    left: 62px;
    top: 220px;
    margin: 0;
    padding: 0;
    list-style: none;
    font-size: 23px;
    color: var(--text-grey);
    line-height: 1.45;
  }
  .contact li {
    display: flex;
    align-items: center;
    gap: 12px;
  }
  .contact .locations {
    display: block;
    margin-bottom: 6px;
  }
  .contact svg {
    width: 20px;
    height: 20px;
    flex: none;
    fill: var(--icon-grey);
  }
</style>
</head>
<body>
<main class="canvas">
  <section class="card" aria-label="BrindlewayCare business card">
    <div class="accent-band"></div>
    <div class="brand-dot"></div>
    <p class="brand-name">BrindlewayCare</p>

    <div class="person">
      <p class="person-name">Derek Mallow</p>
      <p class="person-title">Executive Chairman</p>
    </div>

    <ul class="contact">
      <li class="locations">United Kingdom,<br>Australia, New Zealand</li>
      <li>
        <svg viewBox="0 0 20 20" aria-hidden="true"><path d="M5 2c1 0 1.6.3 2 1.3l1 2.6c.3.8 0 1.4-.7 1.9l-.9.6c.8 1.7 2.1 3 3.8 3.8l.6-.9c.5-.7 1.1-1 1.9-.7l2.6 1c1 .4 1.3 1 1.3 2 0 2-1.6 3.4-3.4 3.2C7.6 17.2 2.8 12.4 1.8 6.8 1.6 4 3 2 5 2z"/></svg>
        <span>01742 918576</span>
      </li>
      <li>
        <svg viewBox="0 0 20 20" aria-hidden="true"><path d="M2 4h16v12H2z M3.5 5.5l6.5 5 6.5-5" fill="none" stroke="#9a8f7e" stroke-width="1.8"/></svg>
        <span>d.mallow@plumvora.example</span>
      </li>
      <li>
        <svg viewBox="0 0 20 20" aria-hidden="true"><circle cx="10" cy="10" r="8" fill="none" stroke="#9a8f7e" stroke-width="1.8"/><path d="M2 10h16M10 2c-3 3-3 13 0 16M10 2c3 3 3 13 0 16" fill="none" stroke="#9a8f7e" stroke-width="1.4"/></svg>
        <span>www.plumvora.example</span>
      </li>
    </ul>
  </section>
</main>
</body>
</html>
```